holloway paving service

Needs to have phone number 0418259730 and email markholloway@brightmail.com.au.
ABN 62318470915
name mark holloway

For all your concreting solutions
Excavation
Exposed & colour concrete
House & shed slabs
Driveways
Landing & steps

Contact Information for Business Card

ph 0418259730
email markholloway@brightmail.com.au.
ABN 62318470915
name mark holloway

```html
<!DOCTYPE html>
<html lang="en">
<head>
<meta charset="utf-8">
<title>Holloway Paving Service – Business Card</title>
<link href="https://fonts.googleapis.com/css2?family=Raleway:wght@600;700&family=Lato:wght@400&display=swap" rel="stylesheet">
<style>
  :root {
    --bg: #2b2b2b;
    --card-white: #ffffff;
    --brand-orange: #f26a21;
    --ink-grey: #5f5f5f;
    --ink-dark: #1d1d1d;
    --rule: #6a6a6a;
  }
  * { margin: 0; padding: 0; box-sizing: border-box; }
  html, body { width: 1200px; height: 1200px; overflow: hidden; }
  body { background: var(--bg); position: relative; font-family: "Lato", sans-serif; }

  .card {
    position: absolute;
    top: 310px;
    height: 594px;
    text-align: center;
  }
  .card--front { left: 234px; width: 364px; background: var(--card-white); }
  .card--back  { left: 627px; width: 369px; background: var(--brand-orange); color: #fff; }

  .brand-mark {
    position: absolute;
    left: 0; right: 0;
    font-family: "Raleway", sans-serif;
    font-weight: 700;
    letter-spacing: 0.5px;
  }
  .brand-mark__square {
    display: block;
    margin: 0 auto 18px;
    background: currentColor;
  }
  .card--front .brand-mark {
    top: 420px - 0px;
    top: 410px;
    color: var(--brand-orange);
    font-size: 27px;
    line-height: 32px;
  }
  .card--front .brand-mark { top: 130px; }
  .card--front .brand-mark__square { width: 34px; height: 34px; }

  .contact { position: absolute; left: 0; right: 0; top: 422px; }
  .contact__name {
    font-family: "Raleway", sans-serif;
    font-weight: 700;
    font-size: 21px;
    line-height: 28px;
    color: var(--ink-grey);
  }
  .contact__name-first { color: var(--brand-orange); }
  .contact__abn { font-size: 17px; color: var(--ink-dark); margin-top: 3px; }
  .contact__rule { width: 207px; height: 1px; background: var(--rule); margin: 14px auto 13px; }
  .contact__line { font-size: 17px; line-height: 22px; color: var(--ink-dark); }

  .card--back .brand-mark {
    top: 200px;
    color: #fff;
    font-size: 34px;
    line-height: 40px;
  }
  .card--back .brand-mark__square { width: 56px; height: 56px; margin-bottom: 24px; }

  .services { position: absolute; left: 0; right: 0; top: 444px; }
  .services__tagline {
    font-family: "Raleway", sans-serif;
    font-weight: 700;
    font-size: 17px;
    line-height: 22px;
    margin-bottom: 8px;
  }
  .services__list { list-style: none; font-size: 17px; line-height: 21.5px; }
</style>
</head>
<body>
  <section class="card card--front" aria-label="Business card front">
    <div class="brand-mark">
      <span class="brand-mark__square"></span>
      HOLLOWAY PAVING<br>SERVICE
    </div>
    <div class="contact">
      <p class="contact__name"><span class="contact__name-first">MARK</span> HOLLOWAY</p>
      <p class="contact__abn">ABN 62318470915</p>
      <div class="contact__rule"></div>
      <p class="contact__line">0418259730</p>
      <p class="contact__line">markholloway@brightmail.com.au</p>
    </div>
  </section>

  <section class="card card--back" aria-label="Business card back">
    <div class="brand-mark">
      <span class="brand-mark__square"></span>
      HOLLOWAY PAVING<br>SERVICE
    </div>
    <div class="services">
      <p class="services__tagline">FOR ALL YOUR CONCRETING<br>SOLUTIONS</p>
      <ul class="services__list">
        <li>Excavation &nbsp;| Exposed &amp; colour concrete</li>
        <li>House &amp; shed slabs &nbsp;| Driveways</li>
        <li>Landing &amp; steps</li>
      </ul>
    </div>
  </section>
</body>
</html>
```